Tavel Website

Need a 4 page Drupal website - Home, About Us, Portfolio, Contact for a private equity/venture capital firm and new logo - company name is Tavel Corporation. The design should communicate - stock markets, hedge funds, deal-making, investments. The Portfolio section is to showcase the small companies we invest in. Hoping for something fresh, dynamic, even fun - no cliche financial images of New York. Not technical - but know how use Drupal content management to make text edits, blocks, articles, etc. We don't use any social media - so no chirply, Pagebook or WorkNode links. We need space for a post heron email sign-up form. Need website uploaded to my Corvane web hosting account. First time user of Sketch Plaza - have 3 other company websites that need refreshing.

```html
<!DOCTYPE html>
<html lang="en">
<head>
<meta charset="utf-8">
<title>Tavel Corporation</title>
<link href="https://fonts.googleapis.com/css2?family=Oswald:wght@400;500&family=Source+Sans+3:wght@400;600;700&display=swap" rel="stylesheet">
<style>
:root{
  --navy:#1c2331;
  --navy-deep:#151b26;
  --navy-field:#2c3444;
  --red:#dc2e26;
  --grey-band:#efefef;
  --text:#333;
  --muted:#555;
  --white:#fff;
}
*{margin:0;padding:0;box-sizing:border-box}
html,body{width:681px;height:1200px;overflow:hidden;background:var(--white)}
body{font-family:"Source Sans 3",Arial,sans-serif;color:var(--text);position:relative}
.abs{position:absolute}
/* header */
.site-header{position:absolute;left:0;top:0;width:681px;height:55px;background:var(--white)}
.brand{position:absolute;left:97px;top:20px;font-size:13px;font-weight:600;color:var(--navy);white-space:nowrap}
.main-nav{position:absolute;left:386px;top:22px;display:flex;align-items:center;font-size:7.5px;font-weight:600;color:var(--navy)}
.main-nav .sep{width:3px;height:3px;border-radius:50%;background:var(--red);margin:0 9px}
.search{position:absolute;left:567px;top:21px}
/* hero */
.hero{position:absolute;left:0;top:55px;width:681px;height:247px;background:var(--navy);overflow:hidden}
.hero-photo{position:absolute;left:300px;top:0;width:381px;height:247px;background:radial-gradient(ellipse at 65% 45%,#4a6a8a 0%,#2b3e56 45%,#1c2331 85%)}
.hero-title{position:absolute;left:91px;top:58px;font-family:"Oswald",sans-serif;font-weight:500;font-size:19px;color:var(--red);letter-spacing:.2px}
.hero-copy{position:absolute;left:88px;top:92px;width:162px;font-size:6.4px;line-height:10.7px;color:#e8ebf0;text-align:justify}
.btn-outline{position:absolute;left:90px;top:172px;width:58px;height:22px;border:1px solid #cfd4dc;border-radius:2px;color:var(--white);font-size:6.8px;display:flex;align-items:center;justify-content:center}
.slide-arrow{position:absolute;top:111px;width:20px;height:22px;background:var(--red);display:flex;align-items:center;justify-content:center}
/* services */
.service{position:absolute;top:326px;width:130px;text-align:center}
.service-icon{width:35px;height:35px;border-radius:50%;background:var(--red);margin:0 auto;display:flex;align-items:center;justify-content:center}
.service h3{font-size:10.5px;font-weight:600;color:#222;margin-top:10px}
.service p{font-size:6px;line-height:10.5px;color:var(--muted);margin-top:5px}
.btn-dark{position:absolute;width:35px;height:17px;background:var(--navy);color:var(--white);font-size:6.4px;display:flex;align-items:center;justify-content:center}
/* about */
.about{position:absolute;left:0;top:477px;width:681px;height:162px;background:var(--grey-band)}
.about-photo{position:absolute;left:92px;top:25px;width:141px;height:84px;border:3px solid var(--white);box-shadow:0 0 0 1px #ddd;background:linear-gradient(135deg,#d9dde0,#b9c0c6 60%,#8f979f)}
.about h2{position:absolute;left:250px;top:24px;font-size:14px;font-weight:400;color:#222}
.about p{position:absolute;left:250px;top:48px;width:341px;font-size:5.9px;line-height:11.6px;color:var(--muted);text-align:justify}
/* portfolio */
.portfolio{position:absolute;left:0;top:639px;width:681px;height:208px;background:var(--red)}
.section-title{position:absolute;left:0;width:681px;text-align:center;font-size:14px;font-weight:400}
.rule{position:absolute;left:330px;width:22px;height:2px}
.tile{position:absolute;top:67px;height:85px;background:var(--white);display:flex;align-items:center;justify-content:center;font-size:11px;font-weight:600;color:var(--navy)}
/* testimonials */
.quote-photo{position:absolute;top:916px;width:61px;height:56px;border:2px solid var(--white);box-shadow:0 0 0 1px #ccc}
.quote{position:absolute;top:921px;width:160px;font-size:6px;line-height:10.6px;color:var(--muted);text-align:justify}
.quote-mark{position:absolute;top:912px;font-size:13px;color:#999;font-family:Georgia,serif}
.quote cite{display:block;font-style:normal;color:var(--red)}
/* newsletter */
.newsletter{position:absolute;left:0;top:1005px;width:681px;height:157px;background:var(--navy)}
.newsletter .lead{position:absolute;left:0;top:42px;width:681px;text-align:center;font-size:6.4px;font-weight:700;color:var(--white)}
.email-field{position:absolute;left:174px;top:73px;width:332px;height:27px;background:var(--navy-field);color:#dfe3ea;font-size:6.6px;padding-left:10px;display:flex;align-items:center}
.btn-red{position:absolute;left:304px;top:114px;width:73px;height:23px;background:var(--red);color:var(--white);font-size:7.5px;display:flex;align-items:center;justify-content:center}
.site-footer{position:absolute;left:0;top:1162px;width:681px;height:38px;background:var(--navy-deep);color:#cfd4dc;font-size:6px;display:flex;align-items:center;justify-content:center}
</style>
</head>
<body>

<header class="site-header">
  <div class="brand">Tavel Corporation</div>
  <nav class="main-nav">
    <span>Home</span><span class="sep"></span><span>About Us</span><span class="sep"></span><span>Portfolio</span><span class="sep"></span><span>Contact</span>
  </nav>
  <svg class="search" width="13" height="13" viewBox="0 0 13 13"><circle cx="5" cy="5" r="3.8" fill="none" stroke="#dc2e26" stroke-width="1.4"/><line x1="7.8" y1="7.8" x2="11.5" y2="11.5" stroke="#dc2e26" stroke-width="1.6"/></svg>
</header>

<section class="hero">
  <div class="hero-photo" role="img" aria-label="Businessman in a suit touching a glowing rising growth chart on a screen"></div>
  <h1 class="hero-title">TAVEL CORPORATION</h1>
  <p class="hero-copy">Vestibulum sit amet neque eu neque suscipit consequat quis vel risus. Vestibulum vehicula purus nec dui accumsan fermentum. Suspendisse potenti. Ut dapibus est id odio pretium blandit in eget leo. Vestibulum sit amet neque eu neque suscipit consequat quis vel risus. Vestibulum vehicula purus nec dui accumsan fermentum.</p>
  <div class="btn-outline">Read More</div>
  <div class="slide-arrow" style="left:0"><svg width="8" height="12" viewBox="0 0 8 12"><polyline points="6.5,1 1.5,6 6.5,11" fill="none" stroke="#fff" stroke-width="2"/></svg></div>
  <div class="slide-arrow" style="left:661px"><svg width="8" height="12" viewBox="0 0 8 12"><polyline points="1.5,1 6.5,6 1.5,11" fill="none" stroke="#fff" stroke-width="2"/></svg></div>
</section>

<section class="services">
  <div class="service" style="left:80px">
    <div class="service-icon"><svg width="16" height="14" viewBox="0 0 16 14"><rect x="1" y="8" width="3" height="5" fill="#fff"/><rect x="6" y="6" width="3" height="7" fill="#fff"/><rect x="11" y="3" width="3" height="10" fill="#fff"/><polyline points="1,6 6,3 9,4 15,0" fill="none" stroke="#fff" stroke-width="1.3"/></svg></div>
    <h3>Stock Market</h3>
    <p>Lorem Ipsum is simply dummy text<br>ing and typesetting industry standard<br>dummy text ever</p>
  </div>
  <div class="service" style="left:212px">
    <div class="service-icon"><svg width="18" height="16" viewBox="0 0 18 16"><text x="0" y="13" font-family="Source Sans 3,sans-serif" font-weight="700" font-size="14" fill="#fff">$</text><g stroke="#fff" stroke-width="1.3"><line x1="9" y1="5" x2="17" y2="5"/><line x1="9" y1="11" x2="17" y2="11"/></g></svg></div>
    <h3>Hedge Funds</h3>
    <p>Lorem Ipsum is simply dummy text<br>ing and typesetting industry standard<br>dummy text ever</p>
  </div>
  <div class="service" style="left:338px">
    <div class="service-icon"><svg width="18" height="12" viewBox="0 0 18 12"><path d="M1 4 L5 1 L9 4 L13 1 L17 4 L12 10 L9 8 L6 10 Z" fill="#fff"/></svg></div>
    <h3>Deal-Making</h3>
    <p>Lorem Ipsum is simply dummy text<br>ing and typesetting industry standard<br>dummy text ever</p>
  </div>
  <div class="service" style="left:477px">
    <div class="service-icon"><svg width="18" height="18" viewBox="0 0 18 18"><circle cx="9" cy="9" r="7.5" fill="none" stroke="#fff" stroke-width="1.5"/><text x="5.6" y="13" font-family="Source Sans 3,sans-serif" font-weight="700" font-size="11" fill="#fff">$</text></svg></div>
    <h3>Investments</h3>
    <p>Lorem Ipsum is simply dummy text<br>ing and typesetting industry standard<br>dummy text ever</p>
  </div>
  <div class="btn-dark" style="left:122px;top:430px">More</div>
  <div class="btn-dark" style="left:251px;top:430px">More</div>
  <div class="btn-dark" style="left:383px;top:430px">More</div>
  <div class="btn-dark" style="left:523px;top:430px">More</div>
</section>

<section class="about">
  <div class="about-photo" role="img" aria-label="Portrait of a smiling executive in a suit and tie"></div>
  <h2>ABOUT TAVEL CORPORATION</h2>
  <p>Vestibulum sit amet neque eu neque suscipit consequat quis vel risus. Vestibulum vehicula purus nec dui accumsan fermentum. Suspendisse potenti. Ut dapibus est id odio pretium blandit in eget leo. Vestibulum sit amet neque eu neque suscipit consequat quis vel risus. Vestibulum vehicula purus nec dui accumsan fermentum. Suspendisse potenti. Ut dapibus est id odio pretium blandit in eget leo. Vestibulum sit amet neque eu neque suscipit consequat quis vel risus. Vestibulum vehicula purus nec dui accumsan fermentum. Suspendisse potenti.</p>
  <div class="btn-dark" style="left:250px;top:114px">More</div>
</section>

<section class="portfolio">
  <h2 class="section-title" style="top:20px;color:var(--white)">OUR PORTFOLIO</h2>
  <div class="rule" style="top:45px;background:var(--white)"></div>
  <div class="tile" style="left:92px;width:94px">Lumora</div>
  <div class="tile" style="left:192px;width:97px">Brightvale</div>
  <div class="tile" style="left:295px;width:92px">Quintel</div>
  <div class="tile" style="left:393px;width:96px">Northwick</div>
  <div class="tile" style="left:493px;width:96px">Solen Bio</div>
  <svg class="abs" style="left:327px;top:173px" width="28" height="14" viewBox="0 0 28 14"><polyline points="8,1 2,7 8,13" fill="none" stroke="#a81a14" stroke-width="2.2"/><polyline points="18,1 24,7 18,13" fill="none" stroke="#fff" stroke-width="2.2"/></svg>
</section>

<section class="testimonials">
  <h2 class="section-title" style="top:871px;color:#222">TESTIMONIALS</h2>
  <div class="rule" style="top:893px;background:var(--navy)"></div>
  <div class="quote-photo" style="left:91px;background:linear-gradient(135deg,#e4ecf2,#9fb8cc)" role="img" aria-label="Smiling man in a light blue shirt"></div>
  <span class="quote-mark" style="left:161px">&ldquo;</span>
  <p class="quote" style="left:171px">Vestibulum sit amet neque eu neque suscipit consequat quis vel risus. Vestibulum vehicula purus nec dui accumsan fermentum. Suspendisse potenti. Ut dapibus est id odio pretium blandit in eget leo. Vestibulum.<cite>- Sam Orrin</cite></p>
  <div class="quote-photo" style="left:350px;background:linear-gradient(135deg,#f1f1f1,#c9c9c9)" role="img" aria-label="Smiling businesswoman in a white blouse"></div>
  <span class="quote-mark" style="left:420px">&ldquo;</span>
  <p class="quote" style="left:430px">Vestibulum sit amet neque eu neque suscipit consequat quis vel risus. Vestibulum vehicula purus nec dui accumsan fermentum. Suspendisse potenti. Ut dapibus est id odio pretium blandit in eget leo. Vestibulum.<cite>- Sam Orrin</cite></p>
</section>

<section class="newsletter">
  <h2 class="section-title" style="top:23px;color:var(--white)">NEWSLETTER SIGNUP</h2>
  <p class="lead">Subscribe to our newsletter to stay update with what is new</p>
  <div class="rule" style="top:57px;background:var(--white)"></div>
  <div class="email-field">Email Address</div>
  <div class="btn-red">SUBSCRIBE</div>
</section>

<footer class="site-footer">Tavel Corporation © copy right 2014 | All Rights Reserved</footer>

</body>
</html>
```